Australian Trucking Company Requires Professional Looking Stationary

We require a professional looking stationary design that incorporates our newly designed logo.

Our business, called "Brell Haulage Contracting", provides contracting work, transport and logistics to business in Western Australia particularly with links to the mining sector.

We are a small business looking to expand and our new logo and our new stationary will help develop our brand image in our market place.

Target Market(s)

Businesses and Corporation with links to the Mining Sector

Industry/Entity Type

Small Business

Requirements
Must have
• The letterhead must have the following details:
The new logo

Text saying: "Brell Holdings Pty Ltd (ACN 582 316 907) ATF The Brell Discretionary Trust T/AS"
"ABN 71 834 209 553"
Address "P.O Box 817 Wattlegrove WA, 6958"
Phone: 08 9352 7140
Email: brellhaul@mailbox-example.com.au

The text on the letterhead should be editable as the details are likely to change in the near future. Provision should be made for a website address all though one isn't available at the moment.

The styling, layout and font text is entirely up to the designer.

```html
<!DOCTYPE html>
<html lang="en">
<head>
<meta charset="utf-8">
<title>Brell Haulage Contracting – Business Cards</title>
<link href="https://fonts.googleapis.com/css2?family=Arimo:wght@400;700&display=swap" rel="stylesheet">
<style>
  :root {
    --brand-red: #8b1a1d;
    --ink-grey: #444444;
    --text-grey: #7a7a7a;
    --band-grey: #4a4a4a;
    --card-white: #ffffff;
    --page-bg: #e9e7e4;
  }
  * { margin: 0; padding: 0; box-sizing: border-box; }
  html, body { width: 1200px; height: 1200px; overflow: hidden; }
  body {
    background: var(--page-bg);
    font-family: "Arimo", Arial, sans-serif;
    position: relative;
  }
  .card {
    position: absolute;
    width: 840px;
    height: 480px;
    background: var(--card-white);
    overflow: hidden;
    box-shadow: 0 2px 8px rgba(0,0,0,0.18);
  }
  .card-front { left: 84px; top: 78px; }
  .card-back { left: 284px; top: 648px; }
  .bands { position: absolute; left: 0; top: 0; width: 840px; height: 480px; }

  .truck-art {
    position: absolute;
    background: linear-gradient(180deg, #9a9a9a 0%, #5a5a5a 60%, #3c3c3c 100%);
    border-radius: 6px;
  }
  .front-truck { left: 58px; top: 64px; width: 198px; height: 162px; }
  .back-truck { left: 20px; top: 56px; width: 330px; height: 312px; }
  .back-truck-faint {
    left: 632px; top: 308px; width: 148px; height: 120px;
    background: linear-gradient(180deg, #e2e2e2 0%, #cfcfcf 100%);
  }

  .company-name {
    position: absolute;
    left: 296px; top: 78px;
    color: var(--brand-red);
    font-weight: 700;
    font-size: 50px;
    line-height: 56px;
    text-transform: uppercase;
    letter-spacing: 1px;
  }

  .contact-list {
    position: absolute;
    left: 36px; top: 296px;
    list-style: none;
    color: var(--ink-grey);
    font-size: 21px;
  }
  .contact-list li { display: flex; align-items: center; height: 34px; }
  .contact-list svg { width: 16px; height: 16px; margin-right: 9px; fill: var(--brand-red); flex: none; }

  .holder {
    position: absolute;
    right: 36px; top: 332px;
    text-align: right;
    color: var(--brand-red);
  }
  .holder-name { font-size: 30px; font-weight: 700; line-height: 36px; }
  .holder-title { font-size: 24px; letter-spacing: 2px; line-height: 34px; }

  .abn {
    position: absolute;
    right: 32px; top: 450px;
    color: #fff;
    font-size: 22px;
  }

  .legal-text {
    position: absolute;
    left: 374px; top: 170px;
    color: var(--text-grey);
    font-size: 22px;
    line-height: 30px;
    white-space: nowrap;
  }

  .web-address {
    position: absolute;
    right: 48px; top: 446px;
    color: #fff;
    font-size: 25px;
    letter-spacing: 2px;
    white-space: nowrap;
  }
  .web-address strong { font-weight: 700; }
</style>
</head>
<body>

<section class="card card-front" aria-label="Business card front">
  <svg class="bands" viewBox="0 0 840 480" aria-hidden="true">
    <polygon points="0,462 410,462 392,480 0,480" fill="#4a4a4a"/>
    <polygon points="440,439 840,439 840,480 396,480" fill="#8b1a1d"/>
  </svg>

  <div class="truck-art front-truck" role="img" aria-label="Grey illustration of a semi-trailer truck cab"></div>

  <div class="company-name">Brell<br>Haulage<br>Contracting</div>

  <ul class="contact-list">
    <li><svg viewBox="0 0 16 16"><path d="M3.5 1.5l2.5 3-1.5 1.8c.9 2 2.3 3.4 4.2 4.3l1.8-1.5 3 2.5-1.6 2.4C6.5 13.6 2.4 9.5 1.1 3.1z"/></svg>08 9352 7140</li>
    <li><svg viewBox="0 0 16 16"><path d="M1 4h14v1L8 9.5 1 5z M1 6.5l7 4.5 7-4.5V12H1z"/></svg>brellhaul@mailbox-example.com.au</li>
    <li><svg viewBox="0 0 16 16"><path d="M8 1a7 7 0 1 0 0 14A7 7 0 0 0 8 1zm0 1.3c.8.8 1.4 2.2 1.6 3.7H6.4C6.6 4.5 7.2 3.1 8 2.3zM2.4 7.2h2.8c0 .6 0 1.1.1 1.6H2.4a5.6 5.6 0 0 1 0-1.6zm4 0h3.2a9 9 0 0 1 0 1.6H6.4a9 9 0 0 1 0-1.6zm4.4 0h2.8a5.6 5.6 0 0 1 0 1.6h-2.8c.1-.5.1-1 0-1.6zM6.4 10h3.2c-.2 1.5-.8 2.9-1.6 3.7-.8-.8-1.4-2.2-1.6-3.7z"/></svg>www.brellhaul-demo.com</li>
    <li><svg viewBox="0 0 16 16"><path d="M8 1.5L0.5 8h2.3v6.5h3.9v-4h2.6v4h3.9V8h2.3z"/></svg>P.O Box 817 Wattlegrove WA, 6958</li>
  </ul>

  <div class="holder">
    <div class="holder-name">Your Name</div>
    <div class="holder-title">Title</div>
  </div>

  <div class="abn">ABN 71 834 209 553</div>
</section>

<section class="card card-back" aria-label="Business card back">
  <svg class="bands" viewBox="0 0 840 480" aria-hidden="true">
    <polygon points="0,0 428,0 386,40 0,40" fill="#8b1a1d"/>
    <polygon points="448,0 840,0 840,18 428,18" fill="#4a4a4a"/>
    <polygon points="0,462 416,462 398,480 0,480" fill="#4a4a4a"/>
    <polygon points="452,438 840,438 840,480 410,480" fill="#8b1a1d"/>
  </svg>

  <div class="truck-art back-truck" role="img" aria-label="Large grey illustration of a semi-trailer truck cab"></div>
  <div class="truck-art back-truck-faint" role="img" aria-label="Faint small truck cab illustration"></div>

  <p class="legal-text">Brell Holdings Pty Ltd (ACN 582 316 907)<br>ATF The Brell Discretionary Trust T/AS</p>

  <div class="web-address">www.<strong>brellhaul-demo</strong>.com</div>
</section>

</body>
</html>
```